Quill Press Oceania needs a website

We require a website design which will be different to the normal websites that you visit. The objective of this website will be a call to action on the last page which will link to our email address so customers can email us their quotation requirements.

An example of how we envisage the look and the pages turning is as a flip books for example: https://www.vidharbor.example/watch?v=KtLmPzQa7Rw&feature=vh.be

page 1: just has our logo on it with the tag "Specialist producing quality printed books to your deadline."

Page 2: Black Page with white text "Black and White Book"
These are produced either digitally or offset on a complete range of stocks

Page 3: Colour books (use an image of your choice) These are also produced either digitally or offset plus we have the choice of web presses for larger print runs

Page 4: Digital books We do have a minimum run of 50 books using this process so a one off Thesis is not economically viable using this process. In special circumstance the digital process can produce books more quickly then by using our offset printing process.

Page 5: Having the complete range of printing machines at our disposal enables you to make a perfectly informed choice for your special project.

Then we need a special quote button which takes them directly to our email link. On this page we also need to add: We have had 25 years' experience printing books saving customers time and money whilst guaranteeing quality

Page 6: Logo repeated from page one with name: Morgan Elsworth and mobile phone no 0487 552 314

- Must follow the brief exactly. Must have a turn page book. Clear, simple and concise with a touch of creative flare and must lead into a call for action which is there quotation. A unique button for quotation link...something out of the ordinary which makes someone want to get a quote.

- It would be nice to have 3D Logo on Page 1 & 6.
a unique button for quotation link...something that make someone eager to proceed.

Our main objective is that they should not leave our website without giving us a quote. Please make sure that the spelling is correct and we do not require clip art images. Continue the logo colours through the theme
Updates

here is another example www.vidharbor.example/watch?v=JbXo412TrGe Added Saturday, May 13, 2017

Target Market(s)

Schools, Universities, Self Publishers, Publishers, Graphic Designers, Conference Providers, Businesses, Corporations, Government.

Industry/Entity Type

Printing

Coding

Coded - Design and coding required

Number of Pages Required

5+ page

Font styles to use
Sans Serif

Colors
34a6d7
ec1f27
fbed22
9bcb3c
ffc214
6b449b

Requirements
Must have
• Must follow the brief exactly. Must have a turn page book. Clear, simple and concise with a touch of creative flare and must lead into a call for action which is there quotation. A unique button for quotation link...something out of the ordinary which makes someone want to get a quote. would like to see the colours of the logo use throughout
Nice to have
• 3D Logo on Page 1 & 6.
• a unique button for quotation link...something that make someone eager to proceed.
• Our main objective is that they should not leave our website without giving us a quote
Should not have
• Spelling mistakes, clip art, ordinary design

```html
<!DOCTYPE html>
<html lang="en">
<head>
<meta charset="utf-8">
<title>Quill Press Oceania – Digital Books</title>
<link rel="stylesheet" href="https://fonts.googleapis.com/css2?family=Fredericka+the+Great&family=Open+Sans:wght@400;600;700&display=swap">
<style>
  :root {
    --stage-dark: #2e2e2e;
    --stage-mid: #4a4a4a;
    --page: #f4f4f4;
    --ink: #2f2f2f;
    --ink-soft: #333333;
    --accent-red: #ec1f27;
    --frame-grey: #c9c9c9;
    --icon-grey: #555555;
  }
  * { box-sizing: border-box; margin: 0; padding: 0; }
  html, body { width: 1200px; height: 720px; overflow: hidden; }
  body { position: relative; background: var(--stage-dark); font-family: "Open Sans", sans-serif; }

  .stage-backdrop {
    position: absolute; inset: 0;
    background:
      linear-gradient(90deg, rgba(46,46,46,.55), rgba(46,46,46,.35) 50%, rgba(46,46,46,.55)),
      linear-gradient(135deg, #6b6e73 0%, #4c4f55 35%, #5d5a58 60%, #3f4246 100%);
  }

  .book {
    position: absolute; left: 133px; top: 24px; width: 935px; height: 672px;
    display: flex;
    box-shadow: 0 12px 30px rgba(0,0,0,.55);
  }
  .page { position: relative; width: 50%; height: 100%; background: var(--page); }
  .page--left { width: 467px; }
  .page--right {
    width: 468px;
    background: linear-gradient(90deg, #d6d6d6 0%, #ececec 5%, var(--page) 12%);
  }

  .reader-icon { position: absolute; left: 177px; top: 25px; width: 116px; height: 154px; }

  .page-heading {
    position: absolute; left: 33px; top: 198px; width: 420px;
    font-family: "Fredericka the Great", serif;
    font-weight: 400; font-size: 31px; line-height: 43.3px;
    color: var(--ink-soft); white-space: nowrap;
  }

  .intro {
    position: absolute; left: 82px; top: 56px; width: 345px;
    font-size: 16px; line-height: 24px; color: var(--ink);
  }

  .quote-button {
    position: absolute; left: 82px; top: 156px; width: 152px; height: 48px;
    display: flex; align-items: center; justify-content: center; gap: 7px;
    background: var(--accent-red); color: #fff; text-decoration: none;
    font-weight: 600; font-size: 16px; border-radius: 2px;
  }
  .quote-button svg { width: 14px; height: 14px; }

  .press-photo {
    position: absolute; left: 82px; top: 244px; width: 250px; height: 224px;
    background: radial-gradient(ellipse at 50% 45%, #9a9aa0 0%, #cfcfd2 55%, var(--page) 75%);
  }

  .experience-box {
    position: absolute; left: 82px; top: 507px; width: 328px; height: 111px;
    border: 2px solid var(--frame-grey);
    display: flex; align-items: center; justify-content: center;
    text-align: center; font-size: 16px; line-height: 24px; color: var(--ink);
    padding: 0 20px;
  }

  .page-curl { position: absolute; right: 0; bottom: 0; width: 24px; height: 24px; }
</style>
</head>
<body>
  <div class="stage-backdrop" role="img" aria-label="Dimmed collage of printing press photographs"></div>

  <div class="book">
    <section class="page page--left">
      <svg class="reader-icon" viewBox="0 0 116 154" aria-hidden="true">
        <rect x="2" y="2" width="112" height="150" rx="9" fill="var(--icon-grey)" stroke="#3c3c3c" stroke-width="3"/>
        <rect x="14" y="14" width="88" height="116" fill="#fff"/>
        <rect x="50" y="139" width="16" height="4" rx="2" fill="#333"/>
        <g stroke="#444" stroke-width="4" stroke-linecap="round">
          <line x1="24" y1="26" x2="92" y2="26"/>
          <line x1="24" y1="37" x2="92" y2="37"/>
          <line x1="24" y1="48" x2="58" y2="48"/>
          <line x1="24" y1="60" x2="92" y2="60"/>
          <line x1="24" y1="72" x2="92" y2="72"/>
          <line x1="24" y1="84" x2="92" y2="84"/>
          <line x1="24" y1="96" x2="92" y2="96"/>
          <line x1="24" y1="108" x2="92" y2="108"/>
          <line x1="24" y1="120" x2="58" y2="120"/>
        </g>
      </svg>
      <h1 class="page-heading">Digital books We do have<br>a minimum run of 50<br>books using this process so<br>a one off Thesis is not eco-<br>nomically viable using this<br>process. In special circum-<br>stance the digital process<br>can produce books more<br>quickly then by using our<br>offset printing process.</h1>
    </section>

    <section class="page page--right">
      <p class="intro">Having the complete range of printing ma-<br>chines at our disposal enables you to make a perfectly informed choice for your special project.</p>
      <a class="quote-button" href="mailto:quotes@quillpress.example">
        <svg viewBox="0 0 14 14" aria-hidden="true">
          <circle cx="7" cy="7" r="7" fill="#fff"/>
          <path d="M4 7h5M7 4.5 9.5 7 7 9.5" fill="none" stroke="var(--accent-red)" stroke-width="1.8" stroke-linecap="round" stroke-linejoin="round"/>
        </svg>
        GET A QUOTE
      </a>
      <div class="press-photo" role="img" aria-label="Wide-format digital printing machine"></div>
      <p class="experience-box">We have had 25 years' experience printing books saving customers time and money whilst guaranteeing quality</p>
      <svg class="page-curl" viewBox="0 0 24 24" aria-hidden="true">
        <path d="M24 0 L24 24 L0 24 Z" fill="var(--stage-dark)"/>
        <path d="M24 0 L0 24 L6 6 Z" fill="#dcdcdc"/>
      </svg>
    </section>
  </div>
</body>
</html>
```